Research and Innovation programme/projects in WOOD based industries

1.Pramenova s.r.o. (offical registered brand name of our company)
-Managing technology development projects
-International cooperation and development European projects
Our company was founded in 2008 and started to work as a counsilary company operating in the section of european funds administrated by Czech republic. Nowadays we are specializing on projects in the sphere of science and research co-financed by EU.Since 6.6.2013 we are registered under European comission for a purpose of broad support of transnational projects.

Target Market(s)

We are primarily focused on european companies, which stand behind the latest research and innovation of sawing, planing, glulam and logging technologies based on wooden materials.

Coding

Coded - Design and coding required

Number of Pages Required

5+ page

Font styles to use
Serif

Colors
cadf82
abd037
9bcb3c
fee18a
ffcf3e
ffc214

Requirements
Must have
• The web will exist in three possible languages in czech, english and Wortana.
• First page : introduction of a company
• Second page : Area of expertise
• Third page: servicies our company provides
• Fourth page: Our partners
• Fifth page: Conditions of our servicies
• Sixth page: Succesful projects
• - we would also love if we had possibility to add videos about our successful projects
• Seventh: Our team
• We are serious company in the sphere of funds and counsilary servicies, that is why we would love to have web design as representative as possible
• Take on mind that that we are specializing on development management, try to apply that on your design
• In the section of contacts, we would love to have photos of our team,
• This is our current site: http://www.pramenova-example.eu/cz/partneri.html
• This is how our concurency sites are lookin. Take these designs as an slight inspiration.
• http://www.lumatrava-example.sk/en/
• https://www2.brenvick-example.com/global/en.html
Nice to have
• Visible logo on the front page for the visitor.
• As a inspiration we provided link for our current web design, but we dont want to copy the current style, just look at the logo and the pages that exists on current web.
• !!!!!!We also uploaded file, where we explain how our cooperation with partner works. Especially in the part 2. section of service. Take that as an ispiration too, or use that to understand, what our company do.
Should not have
• We are serious company in the sphere of funds and counsilary servicies, that is why we would love to have web design representative as possible

```html
<!DOCTYPE html>
<html lang="en">
<head>
<meta charset="utf-8">
<title>1. Pramenova sro – Beratungsfirma</title>
<link href="https://fonts.googleapis.com/css2?family=Poppins:wght@300;400;500;600&family=Rubik:wght@500;700&display=swap" rel="stylesheet">
<style>
:root{
  --green:#8cc63e;
  --green-dark:#7ab82f;
  --yellow:#fddc7a;
  --yellow-deep:#ffcf3e;
  --ink:#2b2b2b;
  --text:#3d3d3d;
  --grey-bg:#f4f1f1;
  --footer:#232323;
  --partner:#2f3a66;
  --white:#fff;
}
*{margin:0;padding:0;box-sizing:border-box}
html,body{width:1200px;height:4870px;overflow:hidden}
body{font-family:"Poppins",sans-serif;color:var(--text);background:var(--white);position:relative}
.abs{position:absolute}
h2,.heading{font-family:"Rubik",sans-serif;font-weight:700;color:var(--ink);letter-spacing:.5px}
.btn{display:inline-block;background:var(--green);color:#fff;font-family:"Rubik",sans-serif;font-weight:700;font-size:15px;letter-spacing:.5px;padding:10px 18px;text-transform:uppercase}
.photo{display:block}
.section-title{position:absolute;left:0;width:1200px;text-align:center;font-size:24px;text-transform:uppercase}
.section-title::after{content:"";display:block;width:80px;height:2px;background:#888;margin:12px auto 0}

/* header */
.brand{left:126px;top:36px;display:flex;align-items:center;gap:16px}
.brand-mark{width:44px;height:30px;background:var(--green)}
.brand-name{font-size:17px;line-height:22px;color:var(--ink)}
.call{left:546px;top:26px;display:flex;gap:10px;align-items:center}
.call small{display:block;font-size:10px;color:#555}
.call b{font-weight:400;font-size:17px;color:var(--ink)}
.coop{left:758px;top:24px;background:var(--green);color:#fff;font-size:12px;font-weight:600;padding:10px 18px}
.lang{left:984px;top:24px;width:82px;height:38px;border:1px solid #ccc;font-size:11px;display:flex;align-items:center;gap:6px;padding-left:10px}
.lang i{width:16px;height:11px;background:#b0b7c9;display:block}
.nav{left:490px;top:88px;display:flex;gap:32px;font-size:12.5px;color:var(--ink);text-transform:uppercase}

/* hero */
.hero{left:0;top:124px;width:1200px;height:540px;background:linear-gradient(110deg,#8b6b4c 0%,#c9a878 30%,#6d6f66 60%,#3e403e 100%)}
.hero-copy{left:655px;top:348px;color:#fff}
.hero-copy p{font-size:25px;font-weight:300;letter-spacing:1px}
.hero-copy h1{font-family:"Rubik",sans-serif;font-size:45px;font-weight:700;letter-spacing:1px;margin:4px 0 14px}
.hero-copy .btn{padding:8px 16px}
.dots{left:546px;top:612px;display:flex;gap:14px;align-items:center}
.dots span{width:9px;height:9px;border-radius:50%;background:#fff}
.dots span.on{width:13px;height:13px;border:2px solid var(--green);background:#fff}

/* about */
.about-photo{left:128px;top:716px;width:520px;height:415px;background:linear-gradient(135deg,#9a9994,#565a58 55%,#bdb6aa)}
.about-box{left:657px;top:716px;width:409px;height:476px;background:var(--yellow);padding:34px 40px}
.about-box h2{font-size:25px;margin-top:4px}
.about-box p{font-size:15px;line-height:23px;margin-top:22px}
.about-box p+p{margin-top:20px}
.about-box .btn{margin-top:38px}
.mini-mark{position:absolute;right:14px;top:12px;width:44px;height:30px;background:var(--green)}

/* expertise */
.expertise{left:0;top:1252px;width:604px;height:538px;background:var(--grey-bg)}
.expertise h2{position:absolute;left:128px;top:56px;font-size:25px}
.expertise .lead{position:absolute;left:128px;top:118px;width:400px;font-size:15px;line-height:23px}
.exp-item{position:absolute;left:128px;display:flex;gap:18px}
.exp-item .ico{width:64px;height:64px;border-radius:50%;background:var(--yellow-deep);display:flex;align-items:center;justify-content:center;flex:none}
.exp-item b{font-family:"Rubik",sans-serif;font-size:14px;color:var(--ink);display:block;margin-top:6px}
.exp-item p{font-size:12px;line-height:17px;width:260px;margin-top:4px}
.exp-photo{left:604px;top:1252px;width:596px;height:538px;background:linear-gradient(150deg,#2c2b28,#8d7a5e 45%,#d9b98c 70%,#4a4742)}
.exp-btn{left:604px;top:1703px;padding:9px 22px}

/* services */
.card{position:absolute;width:224px;height:207px;background:#fff;box-shadow:0 2px 10px rgba(0,0,0,.09);text-align:center;font-size:14.5px;line-height:24px;color:var(--ink)}
.card .ico{width:70px;height:70px;border-radius:50%;background:var(--yellow);margin:36px auto 16px;display:flex;align-items:center;justify-content:center}
.card.all{background:var(--green);color:#fff;font-family:"Rubik",sans-serif;font-weight:700;font-size:17px;line-height:26px;box-shadow:none}

/* partners */
.partners{left:0;top:2455px;width:1200px;height:311px;background:var(--grey-bg)}
.partner{position:absolute;top:150px;width:210px;height:36px;font-size:25px;font-weight:500;color:var(--partner);display:flex;align-items:center;justify-content:center;gap:10px;white-space:nowrap}
.partner i{display:block;width:20px;height:20px;border-radius:50%;background:#c8102e;flex:none}
.arrow{position:absolute;color:#999;font-size:30px;font-weight:300}

/* conditions */
.cond-yellow{left:0;top:2766px;width:638px;height:604px;background:var(--yellow)}
.cond-photo{left:128px;top:2836px;width:627px;height:464px;background:linear-gradient(160deg,#d5d6d1,#8b8e8a 45%,#6b5a46 80%,#a3866a)}
.cond-card{left:634px;top:2866px;width:430px;height:402px;background:#fff;box-shadow:0 4px 24px rgba(0,0,0,.1);padding:48px 52px}
.cond-card h2{font-size:25px;line-height:32px}
.cond-card p{font-size:15px;line-height:23px;margin-top:22px}
.cond-card .btn{margin-top:26px}

/* projects */
.projects{left:0;top:3370px;width:1200px;height:545px;background:linear-gradient(180deg,#eeeeee,#f3f3f3)}
.proj{position:absolute;top:160px;height:226px;background:linear-gradient(160deg,#b7c3cf,#7b8576 60%,#4a4f46)}
.proj span{position:absolute;left:0;right:0;bottom:0;background:rgba(20,20,20,.55);color:#fff;font-family:"Rubik",sans-serif;font-weight:700;font-size:12px;padding:10px 14px}

/* team */
.member{position:absolute;top:4052px;width:303px;height:440px}
.member .face{height:253px;background:linear-gradient(180deg,#aab0b2,#6f6a64)}
.member .info{height:187px;background:var(--yellow);padding:24px 26px;font-size:12px;line-height:18px;color:var(--ink);position:relative}
.member .info b{font-family:"Rubik",sans-serif;font-size:15px;display:block;text-transform:uppercase;margin-bottom:2px}
.member .corner{position:absolute;right:0;bottom:0;width:0;height:0;border-left:38px solid transparent;border-bottom:38px solid var(--green)}

/* footer */
.footer{left:0;top:4512px;width:1200px;height:358px;background:var(--footer);color:#ddd}
.f-brand{position:absolute;left:146px;top:112px;display:flex;align-items:center;gap:22px}
.f-brand span{font-size:17px;line-height:22px;color:#eee}
.f-col{position:absolute;top:56px;font-size:11px;line-height:18px}
.f-col h4{font-size:11px;font-weight:600;color:#fff;letter-spacing:.5px;margin-bottom:16px}
.f-row{display:flex;gap:12px;margin-bottom:12px}
.soc{display:flex;gap:12px;align-items:center;margin-bottom:14px}
.soc i{display:block;width:26px;height:26px;border-radius:50%;background:#2a6fb5}
.copy{position:absolute;top:316px;left:0;width:1200px;text-align:center;font-size:10px;color:#bbb}
</style>
</head>
<body>

<!-- header -->
<div class="abs brand"><div class="brand-mark"></div><div class="brand-name">1. Pramenova sro<br>Beratungsfirma</div></div>
<div class="abs call">
  <svg width="26" height="26" viewBox="0 0 24 24"><path d="M6.6 10.8a15 15 0 0 0 6.6 6.6l2.2-2.2a1 1 0 0 1 1-.25 11.4 11.4 0 0 0 3.6.57 1 1 0 0 1 1 1V20a1 1 0 0 1-1 1A17 17 0 0 1 3 4a1 1 0 0 1 1-1h3.5a1 1 0 0 1 1 1c0 1.25.2 2.45.57 3.57a1 1 0 0 1-.25 1z" fill="none" stroke="#8cc63e" stroke-width="1.6"/></svg>
  <div><small>CALL US NOW</small><b>+420 700 100 200</b></div>
</div>
<div class="abs coop">CALLS FOR COOPERATION</div>
<div class="abs lang"><i></i>EN <span style="margin-left:14px">▾</span></div>
<nav class="abs nav"><span>The enterprise</span><span>Services</span><span>Projects</span><span>Cooperation partners</span><span>Contact</span></nav>

<!-- hero -->
<div class="abs hero photo" role="img" aria-label="Workshop worker carrying a wooden door panel next to woodworking machines"></div>
<div class="abs hero-copy"><p>WELCOME TO</p><h1>PRAMENOVA SRO</h1><span class="btn">Read more</span></div>
<div class="abs dots"><span></span><span></span><span class="on"></span><span></span><span></span></div>

<!-- about -->
<div class="abs about-photo photo" role="img" aria-label="Industrial wood planing machine in a workshop"></div>
<div class="abs about-box">
  <div class="mini-mark"></div>
  <h2>ABOUT US</h2>
  <p>We start with the administration of EU projects and state aid projects. At present we are working for completed portfolio of clients as supervisors of development and innovative projects.</p>
  <p>The company 1.Pramenova is registered since 04.04.2008 in the commercial register under ID: 10203040.</p>
  <span class="btn">Read more</span>
</div>

<!-- expertise -->
<section class="abs expertise">
  <h2>AREA OF EXPERTISE</h2>
  <p class="lead">Lorem ipsum dolor sit amet consectetur adipiscing elit, sed do eiusmod tempor incididunt ut labore et dolore magna aliqua.</p>
  <div class="exp-item" style="top:224px"><div class="ico"><svg width="30" height="30" viewBox="0 0 24 24"><circle cx="12" cy="12" r="7" fill="#2b2b2b"/><circle cx="12" cy="12" r="3" fill="#ffcf3e"/><path d="M11 2h2v4h-2zM11 18h2v4h-2zM2 11h4v2H2zM18 11h4v2h-4z" fill="#2b2b2b"/></svg></div><div><b>LOREM IPSUM</b><p>Lorem ipsum dolor sit amet consectetur adipiscing elit, sed do</p></div></div>
  <div class="exp-item" style="top:318px"><div class="ico"><svg width="28" height="28" viewBox="0 0 24 24"><path d="M5 3h10v4h-6v10h10v4H5z" fill="#2b2b2b"/></svg></div><div><b>LOREM IPSUM</b><p>Lorem ipsum dolor sit amet consectetur adipiscing elit, sed do</p></div></div>
  <div class="exp-item" style="top:416px"><div class="ico"><svg width="30" height="30" viewBox="0 0 24 24"><path d="M4 20 18 6l2 2L6 22z" fill="#fff"/><path d="M16 4l4 4" stroke="#fff" stroke-width="2"/></svg></div><div><b>LOREM IPSUM</b><p>Lorem ipsum dolor sit amet consectetur adipiscing elit, sed do</p></div></div>
</section>
<div class="abs exp-photo photo" role="img" aria-label="Close-up of a wooden board passing through machine rollers"></div>
<span class="abs btn exp-btn">Read more</span>

<!-- services -->
<h2 class="section-title" style="top:1856px">Our services</h2>
<div class="card" style="left:128px;top:1953px"><div class="ico"><svg width="38" height="38" viewBox="0 0 24 24"><path d="M4 20 16 4l4 3L8 23z" fill="#2b2b2b"/></svg></div>Project<br>Coordination</div>
<div class="card" style="left:367px;top:1953px"><div class="ico"><svg width="38" height="38" viewBox="0 0 24 24"><circle cx="14" cy="7" r="5" fill="#2b2b2b"/><path d="M2 16h6l4 2h6l4-3v3l-5 4H8l-6-2z" fill="#2b2b2b"/></svg></div>Project<br>Financing</div>
<div class="card" style="left:603px;top:1953px"><div class="ico"><svg width="38" height="38" viewBox="0 0 24 24"><path d="M7 4v14M7 4 4 7M7 4l3 3M17 20V6M17 20l-3-3M17 20l3-3" stroke="#2b2b2b" stroke-width="2" fill="none"/></svg></div>Technology and<br>foreign trade projects</div>
<div class="card" style="left:839px;top:1953px"><div class="ico"><svg width="38" height="38" viewBox="0 0 24 24"><rect x="3" y="9" width="18" height="4" fill="#2b2b2b"/><rect x="6" y="13" width="12" height="7" fill="none" stroke="#2b2b2b" stroke-width="2"/><path d="M8 4h8v5H8z" fill="#2b2b2b"/></svg></div>Projects in the framework<br>of international cooperation</div>
<div class="card" style="left:128px;top:2172px"><div class="ico"><svg width="38" height="38" viewBox="0 0 24 24"><rect x="3" y="7" width="18" height="13" rx="2" fill="none" stroke="#2b2b2b" stroke-width="2"/><path d="M9 7V4h6v3" stroke="#2b2b2b" stroke-width="2" fill="none"/></svg></div>EU projects</div>
<div class="card" style="left:367px;top:2172px"><div class="ico"><svg width="38" height="38" viewBox="0 0 24 24"><circle cx="12" cy="12" r="9" fill="none" stroke="#2b2b2b" stroke-width="2"/><ellipse cx="12" cy="12" rx="4" ry="9" fill="none" stroke="#2b2b2b" stroke-width="1.6"/><path d="M3 12h18M5 7h14M5 17h14" stroke="#2b2b2b" stroke-width="1.6"/></svg></div>International<br>Development Projects</div>
<div class="card" style="left:603px;top:2172px"><div class="ico"><svg width="38" height="38" viewBox="0 0 24 24"><path d="M6 3h9l4 4v14H6z" fill="none" stroke="#2b2b2b" stroke-width="2"/><path d="M9 13h8M9 13l3-3M9 13l3 3" stroke="#2b2b2b" stroke-width="2" fill="none"/></svg></div>Export Promotion</div>
<div class="card all" style="left:839px;top:2172px"><svg width="42" height="20" viewBox="0 0 42 20" style="margin:58px auto 10px;display:block"><path d="M2 10h36M30 3l8 7-8 7" stroke="#fff" stroke-width="2" fill="none"/></svg>VIEW ALL<br>SERVICES</div>

<!-- partners -->
<section class="abs partners">
  <h2 class="section-title" style="top:58px">Our partners</h2>
  <span class="arrow" style="left:56px;top:140px">‹</span>
  <div class="partner" style="left:124px"><i></i>Ostrova Invest</div>
  <div class="partner" style="left:384px">Exportalis</div>
  <div class="partner" style="left:618px">Wortana</div>
  <div class="partner" style="left:866px">Lexelia</div>
  <span class="arrow" style="left:1118px;top:140px">›</span>
</section>

<!-- conditions -->
<div class="abs cond-yellow"></div>
<div class="abs cond-photo photo" role="img" aria-label="Timber production hall with stacked lumber"></div>
<div class="abs cond-card">
  <h2>CONDITIONS OF<br>OUR SERVICES</h2>
  <p>Minim veniam, quis nostrud exercitation ullamco laboris nisi ut aliquip ex ea commodo consequat. Duis aute irure dolor in reprehenderit in voluptate velit esse cillum dolore eu fugiat nulla pariatur. Excepteur sint occaecat cupidatat non proident.</p>
  <span class="btn">Read more</span>
</div>

<!-- projects -->
<section class="abs projects">
  <h2 class="section-title" style="top:84px">Successful projects</h2>
  <span class="arrow" style="left:64px;top:250px">‹</span>
  <div class="proj photo" style="left:117px;width:235px" role="img" aria-label="Forestry tractor parked outside"><span>LOREM IPSUM</span></div>
  <div class="proj photo" style="left:361px;width:234px" role="img" aria-label="Industrial building with loading gates"><span>LOREM IPSUM</span></div>
  <div class="proj photo" style="left:605px;width:232px" role="img" aria-label="Renovated interior room"><span>LOREM IPSUM</span></div>
  <div class="proj photo" style="left:845px;width:235px" role="img" aria-label="Apartment building under construction"><span>LOREM IPSUM</span></div>
  <span class="arrow" style="left:1114px;top:250px">›</span>
  <span class="btn" style="position:absolute;left:504px;top:434px;padding:10px 24px">View all projects</span>
</section>

<!-- team -->
<h2 class="section-title" style="top:3970px">Our team</h2>
<div class="member" style="left:128px"><div class="face photo" role="img" aria-label="Portrait of the managing director"></div><div class="info"><b>Geschäftsführer</b>Geschäftsführer<br><br>T: +420 700 100 200<br>F: +420 500 100 300<br>e-mail: office@pramenova-example.eu<br>Die Sprache ihrer Wahl ist English<span class="corner"></span></div></div>
<div class="member" style="left:447px"><div class="face photo" role="img" aria-label="Portrait of the project manager"></div><div class="info"><b>Mgr. Lenka Dvorská</b>Project manager<br><br>T: +420 700 100 211<br>Email: dvorska@pramenova-example.eu<br>Die Sprache ihrer Wahl ist English<span class="corner"></span></div></div>
<div class="member" style="left:763px"><div class="face photo" role="img" aria-label="Portrait of the project consultant"></div><div class="info"><b>Ondrej Brabcovec</b>Projektberater<br><br>T +420 700 100 222<br>Email: brabcovec@pramenova-example.eu<br>Die Sprache ihrer Wahl ist English<span class="corner"></span></div></div>

<!-- footer -->
<footer class="abs footer">
  <div class="f-brand"><div class="brand-mark"></div><span>1. Pramenova sro<br>Beratungsfirma</span></div>
  <div class="f-col" style="left:434px">
    <h4>CONTACT US</h4>
    <div class="f-row"><svg width="10" height="14" viewBox="0 0 10 14"><path d="M5 0a5 5 0 0 1 5 5c0 4-5 9-5 9S0 9 0 5a5 5 0 0 1 5-5z" fill="#ddd"/></svg><span>Pramenova s.r.o, ID 10203040<br>Lindenweg 4, 01000 Altstadt</span></div>
    <div class="f-row"><svg width="11" height="11" viewBox="0 0 24 24"><path d="M6.6 10.8a15 15 0 0 0 6.6 6.6l2.2-2.2 5.6 1.3V21A18 18 0 0 1 3 3h4.5l1.3 5.6z" fill="#ddd"/></svg><span>+420 700 100 222</span></div>
    <div class="f-row"><svg width="11" height="9" viewBox="0 0 11 9"><rect width="11" height="9" fill="#ddd"/><path d="M0 0l5.5 5L11 0" stroke="#232323" fill="none"/></svg><span>info@pramenova-example.eu</span></div>
  </div>
  <div class="f-col" style="left:694px">
    <h4>MENU</h4>
    DAS UNTERNEHMEN<br>SERVICES<br>UNSERE PROJEKTE<br>KOOPERATIONSPARTNER<br>ANRUFE FÜR DIE ZUSAMMENARBEIT<br>CONTACT
  </div>
  <div class="f-col" style="left:950px">
    <h4>CONNECT WITH US</h4>
    <div class="soc"><i></i>Friendloop</div>
    <div class="soc"><i style="background:#1da1f2"></i>Chirpline</div>
    <div class="soc"><i style="background:#232323;border:1px solid #555"></i>Worknet</div>
  </div>
  <div class="copy">Copyright © 2019 All Rights Reserved</div>
</footer>

</body>
</html>
```